FOOD BRAND NEEDS A PUMPKIN SEEDS STAND UP BAG DESIGN

We need the design of a stand up bag (front, back , and bottom) The main product is Pumkin seeds , roasted & sea salted. But it needs to be versatile since it will be adapted to different flavors , sizes, and some other variations.
The size of the bag is 23cm x 33cm x 9cm.
It needs a window for the product so people can see what they are buying, This window can be any shape and origanility is encouraged.
We would also need a mock up front and back with white background.
We appreciate the effort from every particpant.
The product hast to be in spanish. Semillas de Calabaza, Tostadas & saladas.
Uploaded logo, bar code, and a label that has all the elements as a reference.

Requirements
Must have
• TOP RIGHT CORNER STAMP, Window .

```html
<!DOCTYPE html>
<html lang="es">
<head>
<meta charset="utf-8">
<title>Semilla de Calabaza – bolsa stand up</title>
<link rel="stylesheet" href="https://fonts.googleapis.com/css2?family=Fredoka:wght@500;600&family=Caveat:wght@500&family=Open+Sans:wght@400;600&display=swap">
<style>
  :root {
    --bg: #ffffff;
    --bag: #d9692c;
    --seal: #ececec;
    --ink-light: #ffffff;
    --ink-soft: #f6d9c4;
    --brown: #7a4a2a;
    --amp: #f0a37a;
    --label-ink: #555555;
    --rule: #e07a3c;
  }
  * { margin: 0; padding: 0; box-sizing: border-box; }
  html, body { width: 898px; height: 1200px; overflow: hidden; background: var(--bg); }
  body { position: relative; font-family: "Open Sans", sans-serif; }

  .bag {
    position: absolute; top: 364px; width: 372px; height: 504px;
    background: var(--bag); border-radius: 4px 4px 6px 6px; overflow: hidden;
  }
  .bag--front { left: 53px; }
  .bag--back { left: 482px; }
  .bag__seal {
    position: absolute; top: 0; left: 0; right: 0; height: 70px;
    background: var(--seal);
  }
  .bag__seal-note {
    position: absolute; top: 22px; width: 100%; text-align: center;
    font-family: "Caveat", cursive; font-size: 12px; color: #555;
  }

  .brand {
    position: absolute; font-family: "Fredoka", sans-serif; font-weight: 600;
    color: var(--ink-light); font-size: 13px; letter-spacing: 0.2px;
  }
  .bag--front .brand { top: 94px; left: 148px; }
  .bag--back .brand { top: 428px; left: 0; width: 100%; text-align: center; }

  .warning-seal { position: absolute; top: 84px; left: 302px; width: 34px; height: 40px; }

  .title { position: absolute; left: 68px; color: var(--ink-light); font-family: "Fredoka", sans-serif; font-weight: 600; }
  .title__top { top: 138px; font-size: 30px; letter-spacing: 8px; }
  .title__main { top: 180px; font-size: 45px; letter-spacing: 5px; }

  .flavor {
    position: absolute; top: 280px; left: 236px; font-family: "Caveat", cursive;
    color: var(--brown); font-size: 20px; line-height: 17px;
  }
  .flavor__amp {
    position: absolute; top: -10px; left: 60px; font-family: "Fredoka", sans-serif;
    font-size: 42px; color: var(--amp); line-height: 1;
  }

  .window { position: absolute; top: 310px; left: 64px; width: 240px; height: 160px; }
  .net { position: absolute; bottom: 30px; left: 180px; font-size: 8px; color: var(--ink-soft); }

  .nutrition {
    position: absolute; top: 110px; left: 35px; width: 202px; height: 225px;
    background: #fff; border-radius: 6px; padding: 6px 8px; color: var(--label-ink);
  }
  .nutrition__title { font-size: 10.5px; color: #333; margin-left: 28px; margin-bottom: 3px; }
  .nutrition table { width: 100%; border-collapse: collapse; font-size: 6.8px; }
  .nutrition td { padding: 1.6px 0; }
  .nutrition td.val { text-align: right; padding-left: 4px; }
  .nutrition tr.rule td { border-top: 1px solid var(--rule); }
  .nutrition td.sub { padding-left: 8px; }

  .back-info {
    position: absolute; top: 118px; left: 249px; width: 92px;
    color: var(--ink-light); font-size: 8.5px; line-height: 13px;
  }
  .back-info p { margin-bottom: 16px; }
  .distributor {
    position: absolute; top: 368px; left: 60px; width: 260px; text-align: center;
    color: var(--ink-soft); font-size: 6px; line-height: 11px; text-transform: uppercase;
  }
  .web { position: absolute; top: 474px; width: 100%; text-align: center; color: var(--ink-soft); font-size: 8.5px; }
</style>
</head>
<body>

<section class="bag bag--front">
  <div class="bag__seal"><p class="bag__seal-note">100% gluten free</p></div>
  <p class="brand">Tierra Alta</p>
  <svg class="warning-seal" viewBox="0 0 34 40" aria-label="Sello de advertencia: exceso sodio">
    <polygon points="10,1 24,1 33,10 33,24 24,33 10,33 1,24 1,10" fill="#222" stroke="#fff" stroke-width="1.5"/>
    <text x="17" y="15" font-size="4.6" fill="#fff" text-anchor="middle" font-family="Open Sans, sans-serif" font-weight="600">EXCESO</text>
    <text x="17" y="21" font-size="4.6" fill="#fff" text-anchor="middle" font-family="Open Sans, sans-serif" font-weight="600">SODIO</text>
    <rect x="1" y="35" width="32" height="4" fill="#222"/>
  </svg>
  <h1 class="title title__top">SEMILLA DE</h1>
  <h2 class="title title__main">CALABAZA</h2>
  <p class="flavor">tostadas<br>saladas<span class="flavor__amp">&amp;</span></p>
  <svg class="window" viewBox="0 0 240 160">
    <defs>
      <linearGradient id="seeds" x1="0" y1="0" x2="1" y2="1">
        <stop offset="0" stop-color="#cdb59a"/>
        <stop offset="0.5" stop-color="#a98a6e"/>
        <stop offset="1" stop-color="#d4bfa5"/>
      </linearGradient>
    </defs>
    <path role="img" aria-label="Ventana con semillas de calabaza tostadas visibles"
      d="M4 6 C60 -4 150 20 198 80 C222 110 222 150 190 156 C140 160 70 120 38 80 C20 56 10 34 4 6 Z"
      fill="url(#seeds)" stroke="#fff" stroke-width="2"/>
  </svg>
  <p class="net">cont.net. 500g</p>
</section>

<section class="bag bag--back">
  <div class="bag__seal"></div>
  <div class="nutrition">
    <p class="nutrition__title">Declaración Nutrimental</p>
    <table>
      <tr><td>Contenido energético por envase</td><td class="val">2940kcal</td><td class="val">12301kJ</td></tr>
      <tr><td>Porción</td><td class="val">25 g</td><td></td></tr>
      <tr><td>Porciones por envase</td><td class="val">4.8</td><td></td></tr>
      <tr class="rule"><td></td><td class="val">Por Porción</td><td class="val">Por 100g</td></tr>
      <tr><td>Contenido energético</td><td class="val">147 kcal</td><td class="val">588kcal</td></tr>
      <tr><td></td><td class="val">615.3kJ</td><td class="val">2462kJ</td></tr>
      <tr class="rule"><td>Proteínas</td><td class="val">8.5g</td><td class="val">34g</td></tr>
      <tr><td>Carbohidratos</td><td class="val">1g</td><td class="val">4g</td></tr>
      <tr><td class="sub">Azúcares</td><td class="val">0g</td><td class="val">0g</td></tr>
      <tr><td class="sub">Azúcares añadidos</td><td class="val">0g</td><td class="val">0g</td></tr>
      <tr class="rule"><td>Fibra dietética</td><td class="val">4.3g</td><td class="val">17g</td></tr>
      <tr><td>Grasas Totales</td><td class="val">10g</td><td class="val">40g</td></tr>
      <tr><td class="sub">Grasas Saturadas</td><td class="val">1.8g</td><td class="val">7g</td></tr>
      <tr><td class="sub">Grasa Poliinsaturada</td><td class="val">3.5g</td><td class="val">14g</td></tr>
      <tr><td class="sub">Grasa Monoinsaturada</td><td class="val">4.5g</td><td class="val">18g</td></tr>
      <tr class="rule"><td>Sodio</td><td class="val">201.3mg</td><td class="val">805mg</td></tr>
    </table>
  </div>
  <div class="back-info">
    <p>INGREDIENTES:<br>Semilla de calabaza,<br>sal de mar.</p>
    <p>Mantener cerrado<br>en un ambiente<br>fresco y seco.</p>
    <p>Fecha de consumo<br>preferente y lote:</p>
  </div>
  <p class="distributor">Distribuido por Distribuidora Mesa Verde S.A. de C.V.<br>Av. de los Fresnos 48, Col. Las Lomas, CP 00000.<br>Hecho en México. Marca registrada</p>
  <p class="brand">Tierra Alta</p>
  <p class="web">www.tierraalta-mx.com</p>
</section>

</body>
</html>
```